Building company buisness cards

We are looking for a sharp modern new look for our business cards.We are a New Zealand based company that specialises in house and land packages.We have attached a photo of the current logo and would like to see if it can be improved somehow if needed.We are open to any colours but we have chosen Black and White at this stage. Feel free to change the font and make the logo smarter looking.Play with the colours and see what looks best.We want a card that looks so good know one will want to throw it away!

Target Market(s)

Building profesonals, home buyers

Industry/Entity Type

Building

Contact Information for Business Card

Garrick Tenwood
0275390628
garrickt@hartvale.co.nz

Font styles to use
Serif
Sans Serif

Colors

Designer to choose colors to be used in the design.

Requirements
Must have
• Just the logo on one side and details on the other
• Clean simple looking card
Nice to have
• Round corners and detail like raised or spot UV
• Something that stands out
Should not have
• To title needed, Director etc

```html
<!DOCTYPE html>
<html lang="en">
<head>
<meta charset="utf-8">
<title>Hartvale Business Card</title>
<link href="https://fonts.googleapis.com/css2?family=Lato:wght@400;700&display=swap" rel="stylesheet">
<style>
  :root {
    --backdrop: #cbcbcb;
    --card: #2b2b2b;
    --emboss: #1e1e1e;
    --emboss-soft: #232323;
    --ink: #f4f4f4;
  }
  * { margin: 0; padding: 0; box-sizing: border-box; }
  html, body { width: 1200px; height: 1200px; overflow: hidden; }
  body {
    background: var(--backdrop);
    font-family: "Lato", sans-serif;
    position: relative;
  }
  .card {
    position: absolute;
    left: 250px;
    width: 708px;
    height: 402px;
    background: var(--card);
    border-radius: 18px;
  }
  .card--front { top: 144px; }
  .card--back { top: 583px; }

  .brand {
    position: absolute;
    display: flex;
    align-items: center;
  }
  .brand__name { font-weight: 700; letter-spacing: -1px; line-height: 1; }
  .brand__mark { border-radius: 50%; flex: none; }

  .card--front .brand { left: 160px; top: 151px; gap: 18px; }
  .card--front .brand__name { font-size: 84px; color: var(--emboss); }
  .card--front .brand__mark { width: 104px; height: 104px; border: 3px solid var(--emboss); }
  .tagline {
    position: absolute;
    left: 164px;
    top: 248px;
    font-size: 17px;
    letter-spacing: 1px;
    color: var(--emboss-soft);
  }

  .card--back .brand { left: 88px; top: 164px; gap: 14px; }
  .card--back .brand__name { font-size: 58px; color: var(--ink); }
  .card--back .brand__mark { width: 72px; height: 72px; border: 2px solid var(--ink); }

  .divider {
    position: absolute;
    left: 396px;
    top: 151px;
    width: 2px;
    height: 106px;
    background: var(--ink);
  }
  .contact {
    position: absolute;
    left: 410px;
    top: 146px;
    color: var(--ink);
  }
  .contact__name { font-size: 30px; line-height: 1.2; }
  .contact__line { font-size: 21px; line-height: 1.3; }
  .contact__phone { margin-top: 22px; }
</style>
</head>
<body>
  <section class="card card--front">
    <div class="brand">
      <span class="brand__name">Hartvale</span>
      <span class="brand__mark"></span>
    </div>
    <p class="tagline">Homes built around you.</p>
  </section>

  <section class="card card--back">
    <div class="brand">
      <span class="brand__name">Hartvale</span>
      <span class="brand__mark"></span>
    </div>
    <span class="divider"></span>
    <div class="contact">
      <p class="contact__name">Garrick Tenwood</p>
      <p class="contact__line contact__phone">0275390628</p>
      <p class="contact__line">garrickt@hartvale.co.nz</p>
    </div>
  </section>
</body>
</html>
```